Business Card Design

We need a business card designed for our new company. Prefer a black card with white logo & writing.

Contact Information for Business Card

Ted Galloway, address: 7-4812 Fernhollow Road, Abbotsford, BC, V3K 8R2, Office Phone: 604-712-3390, Cell: 604-947-2164, Email: ted@resinworkshub.ca

Colors

Designer to choose only greyscale colors for use in the design.

```html
<!DOCTYPE html>
<html lang="en">
<head>
<meta charset="utf-8">
<title>Resinworks Hub – Business Card</title>
<link href="https://fonts.googleapis.com/css2?family=Poppins:wght@300;400;700&display=swap" rel="stylesheet">
<style>
  :root {
    --backdrop: #e4e4e4;
    --card: #232427;
    --card-shade: #1c1d20;
    --pattern-light: #2a2b2f;
    --ink: #ffffff;
    --ink-soft: #d9d9d9;
  }
  * { margin: 0; padding: 0; box-sizing: border-box; }
  html, body {
    width: 1200px; height: 780px; overflow: hidden;
    background: var(--backdrop);
    font-family: "Poppins", sans-serif;
  }
  .canvas {
    position: relative; width: 1200px; height: 780px;
    display: flex; align-items: center; justify-content: center; gap: 40px;
  }
  .card {
    position: relative; width: 545px; height: 312px;
    background: var(--card); color: var(--ink);
    border-radius: 4px; overflow: hidden;
    box-shadow: 0 8px 22px rgba(0,0,0,.22);
  }

  /* Front */
  .identity {
    position: absolute; left: 30px; top: 28px;
    padding-left: 12px; border-left: 4px solid var(--ink);
  }
  .identity__name { font-size: 27px; line-height: 1.05; font-weight: 300; }
  .identity__name strong { font-weight: 700; }
  .identity__title { font-size: 12px; font-weight: 300; color: var(--ink-soft); margin-top: 3px; }

  .address {
    position: absolute; left: 46px; top: 112px;
    font-size: 12.5px; font-weight: 300; line-height: 1.45; color: var(--ink-soft);
  }
  .contacts {
    position: absolute; left: 30px; top: 168px; list-style: none;
    font-size: 12.5px; font-weight: 300; color: var(--ink-soft);
  }
  .contacts li { display: flex; align-items: center; gap: 8px; height: 20px; }
  .contacts svg { width: 11px; height: 11px; fill: none; stroke: var(--ink); stroke-width: 1.6; }

  .brand {
    position: absolute; right: 34px; bottom: 44px;
    display: flex; align-items: center; gap: 10px;
  }
  .brand__mark { width: 18px; height: 18px; background: var(--ink); }
  .brand__name {
    font-size: 30px; font-weight: 700; line-height: 1; letter-spacing: .5px; color: var(--ink);
  }

  /* Back */
  .card--back .pattern {
    position: absolute; inset: 0;
    background: linear-gradient(135deg, var(--card-shade), var(--pattern-light) 55%, var(--card-shade));
  }
  .card--back .brand {
    right: auto; bottom: auto; left: 50%; top: 50%;
    transform: translate(-50%, -50%);
  }
</style>
</head>
<body>
<main class="canvas">
  <section class="card card--front">
    <div class="identity">
      <h1 class="identity__name"><strong>Ted</strong> Galloway</h1>
      <p class="identity__title">Founder &amp; CEO</p>
    </div>
    <p class="address">7-4812 Fernhollow Road,<br>Abbotsford, BC, V3K 8R2.</p>
    <ul class="contacts">
      <li>
        <svg viewBox="0 0 12 12"><path d="M2.5 1.5l2 .3.6 2.3-1.2.9a6 6 0 0 0 3.1 3.1l.9-1.2 2.3.6.3 2a1.5 1.5 0 0 1-1.5 1.2A8.5 8.5 0 0 1 1.3 3a1.5 1.5 0 0 1 1.2-1.5z"/></svg>
        604-712-3390
      </li>
      <li>
        <svg viewBox="0 0 12 12"><rect x="3" y="1" width="6" height="10" rx="1"/><path d="M5.3 9h1.4"/></svg>
        604-947-2164
      </li>
      <li>
        <svg viewBox="0 0 12 12"><circle cx="6" cy="6" r="4.8"/><path d="M1.2 6h9.6M6 1.2c-2.2 2.6-2.2 7 0 9.6M6 1.2c2.2 2.6 2.2 7 0 9.6"/></svg>
        www.resinworkshub.ca
      </li>
      <li>
        <svg viewBox="0 0 12 12"><rect x="1" y="2.5" width="10" height="7" rx=".8"/><path d="M1.3 3l4.7 3.7L10.7 3"/></svg>
        ted@resinworkshub.ca
      </li>
    </ul>
    <div class="brand">
      <span class="brand__mark"></span>
      <span class="brand__name">RESINWORKS HUB</span>
    </div>
  </section>

  <section class="card card--back">
    <div class="pattern" role="img" aria-label="Faint repeating brand pattern across the card back"></div>
    <div class="brand">
      <span class="brand__mark"></span>
      <span class="brand__name">RESINWORKS HUB</span>
    </div>
  </section>
</main>
</body>
</html>
```